Broschüre für Gründerberatung
Zielgruppe
Gründerberatung, Co-Working Space
Zielgruppe: Förderer/Sponsoren, Unternehmen im innovativen Kontext
Hallo liebe Designer,
nach mehreren Jahren brauchen wir ein neue Broschüre, die wir potentiellen Förderern und Sponsoren an die Hand geben möchten. Hier stellen wir uns ein modernes, frisches Design vor.
Im ersten Schritt haben wir unser Logo mit neuen Farben designen lassen, worauf nun die neue Broschüre abgestimmt werden soll.
Die Fotos für die Broschüre liefern wir selbst.
Die Texte müssen von uns noch geschrieben werden.
Wir möchten nicht all zu viel vorgeben, abgesehen vom Format und Aufteilung der Seiten.
DIN A4 Hochformat pro Seite , 6 Seiten zum Aufklappen, nicht als Leporello,
Schriftart Trebuchet MS (bitte nicht schwarz)
Farbschema:
Adobe:
Hellgrau: #427881
RGB 66, 120, 129
HSV 189, 49, 51
CMYK 49, 7, 0, 49
LAB 47, -15, -10
Dunkelgrau: #324C52
RGB 50, 76, 82
HSV 191, 39, 32
CMYK 39, 7, 0, 68
LAB 31, -8, -7
Weiß: #FFFF
RGB 255, 255, 255
HSV 0, 0, 100
CMYK 0, 0, 0, 0
LAB 100, 0, 0
Lila: #E018FF . (Diese Farbe, bitte sehr reduziert verwenden)
RGB 224, 24, 255
HSV 292, 91, 100
CMYK 12, 91, 0, 0
LAB 56, 92, -68
Grün:#83FF00
RGB 131, 255, 0
HSV 89, 100, 100
CMYK 49, 0, 100, 0
LAB 90, -67, 86
Das Logo schicken wir als jpg. mit
Außerdem schicken wir ein Foto der alten Broschüre für die Beschriftung der Seitenzahlen mit. Diese Vorlage soll aber kein Hinweis für das neue Design liefern.
Aufteilung der Seiten:
Seite 1:
1 Überschrift
Vorstellung des Unternehmens
25% Text
75% Bilder/Piktogramme
Seite 2:
kurzer Fließtext
30%Text
70 % Fotos/Piktogramme
Seite 3:
zweigeteilt /horizontal
oben:
darunter zwei Fotos mit Zitaten
unten:
2-3 Fotos mit 'Sprechblasen
Seite 4
nur Fotos mit Kurzbeschreibung sollen Atmosphäre vermitteln
Seite 5 (RÃ..

```html
<!DOCTYPE html>
<html lang="de">
<head>
<meta charset="utf-8">
<title>GZR Broschüre – Co-Working</title>
<link href="https://fonts.googleapis.com/css2?family=Oswald:wght@300;400&family=PT+Sans:wght@400;700&display=swap" rel="stylesheet">
<style>
:root{
  --teal:#427881;
  --teal-dark:#324C52;
  --white:#ffffff;
  --green:#83FF00;
  --purple:#E018FF;
  --paper:#f3f4f3;
  --stage:#e9eaea;
  --text:#4a5d61;
}
*{box-sizing:border-box;margin:0;padding:0}
html,body{width:771px;height:1200px;overflow:hidden;background:var(--stage)}
body{position:relative;font-family:"PT Sans",sans-serif;color:var(--text)}
.head{font-family:"Oswald",sans-serif;font-weight:400;text-transform:uppercase;line-height:1.05;color:var(--teal)}
.sub{font-family:"Oswald",sans-serif;font-weight:300;text-transform:uppercase;color:var(--teal);line-height:1.2}
.rule{height:1px;background:var(--teal)}
.body-copy{font-size:4.8px;line-height:1.45;color:var(--text)}
.body-copy p+p{margin-top:4px}
.page{position:absolute;overflow:hidden;box-shadow:0 4px 14px rgba(0,0,0,.18)}
.photo{position:absolute}
.brand{display:flex;align-items:center;gap:5px;font-family:"PT Sans",sans-serif;font-weight:700;color:var(--teal);white-space:nowrap}
.brand-dot{border-radius:50%;background:var(--green);flex:none}

/* primary mark */
.brand-hero{position:absolute;left:80px;top:95px;font-size:56px;gap:14px}
.brand-hero .brand-dot{width:40px;height:40px}

/* cover */
.cover{left:460px;top:110px;width:235px;height:335px;background:linear-gradient(160deg,#c9cdcd,#9ea4a4 55%,#7d8483)}
.cover-title{position:absolute;left:2px;top:0;height:335px;writing-mode:vertical-rl;transform:rotate(180deg);font-family:"Oswald",sans-serif;font-weight:400;font-size:60px;line-height:1;color:var(--teal-dark);opacity:.85;letter-spacing:1px;text-align:center;white-space:nowrap}
.cover-brand-box{position:absolute;right:0;top:0;width:118px;height:66px;background:var(--white);display:flex;align-items:center;justify-content:center}
.cover-brand-box .brand{font-size:15px}
.cover-brand-box .brand-dot{width:12px;height:12px}
.cover-brand-sub{font-size:4.5px;line-height:1.1;font-weight:400;color:var(--teal-dark);border-left:1px solid var(--teal-dark);padding-left:3px}
.cover-claim{position:absolute;left:62px;top:216px;width:153px;height:107px;background:rgba(131,255,0,.72);padding:30px 0 0 33px}
.cover-claim .head{color:var(--white);font-size:14.5px;font-weight:300;line-height:1.1}
.cover-url{font-family:"Oswald",sans-serif;font-weight:300;font-size:7px;color:var(--white);margin-top:10px}
.cover-edge{position:absolute;right:0;top:0;width:4px;height:100%;background:var(--teal-dark)}

/* intro page */
.intro{left:30px;top:470px;width:230px;height:326px;background:var(--paper)}
.intro .brand{position:absolute;right:18px;top:22px;font-size:13px}
.intro .brand-dot{width:10px;height:10px}
.intro-text{position:absolute;left:80px;top:80px;width:132px}
.intro-text .head{font-size:12px}
.intro-text .sub{font-size:6.5px;margin-top:3px}
.intro-text .rule{width:28px;margin:10px 0 8px}

/* co-working page */
.cowork{left:270px;top:470px;width:230px;height:326px;background:linear-gradient(150deg,#5fb81a,#3d7e14 50%,#1f4a12)}
.cowork-title{position:absolute;left:10px;bottom:16px;font-family:"Oswald",sans-serif;font-weight:400;font-size:42px;color:var(--white);line-height:1;letter-spacing:.5px;white-space:nowrap}

/* team page */
.team{left:510px;top:470px;width:230px;height:326px;background:var(--teal-dark)}
.team svg.bg{position:absolute;inset:0}
.team-head{position:absolute;left:62px;top:18px;width:160px}
.team-head .head{color:var(--white);font-size:13px}
.team-head .sub{color:#b7cfd3;font-size:6px;margin-top:3px}
.team-head .rule{background:var(--green);width:28px;margin-top:7px}
.team-strip{position:absolute;top:86px;width:62px;height:26px;background:linear-gradient(90deg,#aab0b2,#6e7779)}
.team-cap{position:absolute;top:116px;width:62px;font-size:3.6px;line-height:1.35;color:#d6e3e5}
.team-cap b{display:block;color:var(--white);font-size:3.8px}
.person{position:absolute;left:16px;display:flex;gap:6px;align-items:center}
.avatar{width:22px;height:22px;border-radius:50%;border:1.5px solid var(--green);background:linear-gradient(135deg,#c2b59f,#6c6458);flex:none}
.person-text{font-size:3.8px;line-height:1.35;color:#cfdcde;width:80px}
.person-text b{display:block;color:var(--white)}
.contact-card{position:absolute;right:0;bottom:0;width:96px;height:60px;background:var(--paper);padding:9px 8px;font-size:4px;line-height:1.4;color:var(--teal-dark)}
.contact-card .brand{font-size:8px;margin-bottom:4px}
.contact-card .brand-dot{width:6px;height:6px}

/* open spread */
.spread{left:62px;top:815px;width:638px;height:300px;background:var(--paper)}
.panel{position:absolute;top:0;height:300px;width:213px}
.panel-1{left:0}
.panel-2{left:213px;border-left:1px solid #dcdedd}
.panel-3{left:426px;border-left:1px solid #dcdedd}
.panel-1 .brand{position:absolute;left:15px;top:22px;font-size:16px}
.panel-1 .brand-dot{width:12px;height:12px}
.p1-text{position:absolute;left:72px;top:64px;width:118px}
.p1-text .head{font-size:13px}
.p1-text .sub{font-size:6.5px;margin-top:3px}
.p1-text .rule{width:30px;margin:10px 0 12px}
.p2-text{position:absolute;left:25px;top:170px;width:170px}
.p2-text .head{font-size:13px}
.p2-text .sub{font-size:6.5px;margin-top:4px}
.p2-text .rule{width:44px;margin:12px 0 14px}
.p3-box{position:absolute;inset:0}
.p3-text{position:absolute;left:48px;top:26px;width:150px}
.p3-text .head{font-size:12.5px}
.p3-copy{position:absolute;left:38px;top:60px;width:95px;text-align:right}
.p3-quote{position:absolute;left:138px;top:92px;width:72px;display:flex;gap:3px}
.p3-quote-bar{width:1.5px;background:var(--purple);flex:none}
.p3-quote-text{font-family:"Oswald",sans-serif;font-weight:300;font-size:5.6px;line-height:1.25;color:#8fa9ad;text-transform:uppercase;white-space:nowrap}
.member{position:absolute;top:185px;width:67px;height:60px;background:#4a5e63;padding:13px 5px 0;text-align:center;color:var(--white)}
.member .avatar{position:absolute;left:50%;top:-15px;margin-left:-15px;width:30px;height:30px;border-width:1.5px}
.member-name{font-size:3.4px;font-weight:700;margin:6px 0 2px}
.member-name span{font-weight:400}
.member p{font-size:3.3px;line-height:1.4;font-style:italic;text-align:left}
.panel-3 .brand{position:absolute;left:30px;bottom:18px;font-size:9px}
.panel-3 .brand-dot{width:7px;height:7px}
.brand-small-sub{font-size:2.8px;font-weight:400;color:var(--teal-dark);line-height:1.1}
</style>
</head>
<body>

<div class="brand brand-hero"><span class="brand-dot"></span>GZR</div>

<section class="page cover">
  <div class="photo" style="inset:0;background:linear-gradient(170deg,rgba(255,255,255,.25),rgba(60,60,60,.2))" role="img" aria-label="Foto: Team im hellen Co-Working-Büro"></div>
  <div class="cover-title">CO-WORKING</div>
  <div class="cover-brand-box">
    <div class="brand"><span class="brand-dot"></span>GZR <span class="cover-brand-sub">Gründerzentrum<br>Rheinau</span></div>
  </div>
  <div class="cover-claim">
    <div class="head">WIR GEBEN IHREN<br>IDEEN RAUM.</div>
    <div class="cover-url">WWW.GZR-RHEINAU.DE</div>
  </div>
  <div class="cover-edge"></div>
</section>

<section class="page intro">
  <div class="brand"><span class="brand-dot"></span>GZR</div>
  <div class="intro-text">
    <div class="head">Hier steht eine<br>Headline zum Thema</div>
    <div class="sub">Ich bin die Subline</div>
    <div class="rule"></div>
    <div class="body-copy">
      <p>Est quate dolorro ommoluptate voloreptate doles esequas quis sincit ulpario. Neque erate re, sam, siti volorer cimodis desto magnis.</p>
      <p>dunditianiet apid quistent inimagnis derro bea ea dolecep taquam dit quis nos eaturitate cus vero ipsusciam re vellaute pre sunt, unda conseque soluptio blanit quodis ut aut ium fuga.</p>
      <p>Evenes alique volum quat. Roribusame dolorrum incil esequi omnim hil ent ma</p>
    </div>
  </div>
  <svg class="photo" style="left:0;top:180px" width="120" height="146" viewBox="0 0 120 146" role="img" aria-label="Foto: Gründer im Gespräch am Besprechungstisch">
    <defs><linearGradient id="g-intro" x1="0" y1="0" x2="1" y2="1"><stop offset="0" stop-color="#c8cbca"/><stop offset="1" stop-color="#5d6766"/></linearGradient></defs>
    <polygon points="0,0 70,0 120,146 0,146" fill="url(#g-intro)"/>
  </svg>
</section>

<section class="page cowork">
  <div class="photo" style="inset:0;background:linear-gradient(200deg,rgba(131,255,0,.35),rgba(0,30,10,.35))" role="img" aria-label="Foto: Arbeitsplätze im Co-Working-Space, grün eingefärbt"></div>
  <div class="cowork-title">CO-WORKING</div>
</section>

<section class="page team">
  <svg class="bg" width="230" height="326" viewBox="0 0 230 326" aria-hidden="true">
    <polygon points="0,0 230,0 230,150 150,200 0,150" fill="var(--teal)"/>
  </svg>
  <div class="team-head">
    <div class="head">Hier steht eine<br>Headline zum Thema</div>
    <div class="sub">Ich bin die Subline</div>
    <div class="rule"></div>
  </div>
  <div class="team-strip" style="left:14px" role="img" aria-label="Foto: Gruppe des Gründerteams"></div>
  <div class="team-strip" style="left:84px" role="img" aria-label="Foto: Gruppe des Beratungsteams"></div>
  <div class="team-strip" style="left:154px" role="img" aria-label="Foto: Gruppe der Förderer"></div>
  <div class="team-cap" style="left:14px"><b>TEAM BERATUNG</b>Begleitung von der Idee bis zur Gründung.</div>
  <div class="team-cap" style="left:84px"><b>TEAM BERATUNG</b>Begleitung von der Idee bis zur Gründung.</div>
  <div class="team-cap" style="left:154px"><b>TEAM BERATUNG</b>Begleitung von der Idee bis zur Gründung.</div>
  <div class="person" style="top:165px"><div class="avatar" role="img" aria-label="Porträtfoto"></div><div class="person-text"><b>NAME NACHNAME</b>Beratung und Förderung für Gründer</div></div>
  <div class="person" style="top:195px"><div class="avatar" role="img" aria-label="Porträtfoto"></div><div class="person-text"><b>NAME NACHNAME</b>Beratung und Förderung für Gründer</div></div>
  <div class="person" style="top:225px"><div class="avatar" role="img" aria-label="Porträtfoto"></div><div class="person-text"><b>NAME NACHNAME</b>Beratung und Förderung für Gründer</div></div>
  <div class="contact-card">
    <div class="brand"><span class="brand-dot"></span>GZR</div>
    GZR Gründerzentrum Rheinau GmbH<br>Hafenstraße 12<br>68219 Rheinau<br>Telefon 0621 123456<br>E-Mail info@gzr-rheinau.de
  </div>
</section>

<section class="page spread">
  <div class="panel panel-1">
    <div class="brand"><span class="brand-dot"></span>GZR</div>
    <div class="p1-text">
      <div class="head">Hier steht eine<br>Headline zum Thema</div>
      <div class="sub">Ich bin die Subline</div>
      <div class="rule"></div>
      <div class="body-copy">
        <p>Est quate dolorro ommoluptate voloreptate doles esequas quis sincit ulpario. Neque erate re, sam, siti volorer cimodis desto magnis.</p>
        <p>dunditianiet apid quistent inimagnis derro bea ea dolecep taquam dit quis nos eaturitate cus vero ipsusciam re vellaute pre sunt, unda conseque soluptio blanit quodis ut aut ium fuga. Ut maionse nobis sedipsum vidis maionse ndelentus, nobitio. Unti re ea nus, sa doluptist alignim erae nonsequam, con et, vellabo. Itasped igenis as iniet et endit ulpa solupta non porem quaspie ndipsam samus vollam quam volumquod que voluptat rem estia simolup tatur?</p>
        <p>Evenes alique volum quat. Roribusame dolorrum incil esequi omnim hil ent ma</p>
      </div>
    </div>
    <svg class="photo" style="left:0;top:235px" width="213" height="65" viewBox="0 0 213 65" role="img" aria-label="Foto: Gründer arbeiten gemeinsam am Laptop">
      <defs><linearGradient id="g-p1" x1="0" y1="0" x2="1" y2="0"><stop offset="0" stop-color="#6b7574"/><stop offset=".6" stop-color="#b9bebd"/><stop offset="1" stop-color="#8c9392"/></linearGradient></defs>
      <polygon points="0,0 175,0 200,65 0,65" fill="url(#g-p1)"/>
    </svg>
  </div>

  <div class="panel panel-2">
    <svg class="photo" style="left:0;top:0" width="213" height="165" viewBox="0 0 213 165" role="img" aria-label="Collage: Menschen im Co-Working-Space und Büroeinrichtung">
      <defs><linearGradient id="g-p2" x1="0" y1="0" x2="1" y2="1"><stop offset="0" stop-color="#c9c7c2"/><stop offset=".5" stop-color="#e2e3e1"/><stop offset="1" stop-color="#8f9694"/></linearGradient></defs>
      <polygon points="0,0 140,0 213,80 213,120 170,165 0,130" fill="url(#g-p2)"/>
      <polygon points="125,8 213,35 213,90 160,120 135,60" fill="var(--green)" opacity=".85"/>
      <polygon points="0,118 40,130 0,140" fill="var(--teal)"/>
    </svg>
    <div class="p2-text">
      <div class="head">Ich bin die Headline</div>
      <div class="sub">Ich bin die Subline,<br>diesmal auf zwei Zeilen</div>
      <div class="rule"></div>
      <div class="body-copy">Est quate dolorro ommoluptate voloreptate doles esequas quis sincit ulpario. Neque erate re, sam, siti volorer cimodis desto magnis. Est quate dolorro ommoluptate voloreptate doles esequas quis sincit ulpario. Neque erate re, sam, siti volorer cimodis desto</div>
    </div>
  </div>

  <div class="panel panel-3">
    <svg class="p3-box" width="213" height="300" viewBox="0 0 213 300" aria-hidden="true">
      <polygon points="22,0 213,0 200,165 22,140" fill="#e3e7e7"/>
    </svg>
    <div class="p3-text"><div class="head">Ich bin die Headline</div></div>
    <div class="p3-copy body-copy">Est quate dolorro ommoluptate voloreptate doles esequas quis sincit ulpario. Neque erate re, sam, siti volorer Est quate dolorro ommoluptate voloreptate doles esequas quis sincit ulpario. Neque erate re, sam, siti volorer cimodis desto magnis. Est quate dolorro ommoluptate voloreptate doles esequas quis sincit ulpario. Neque erate re, sam, siti vol</div>
    <div class="p3-quote">
      <span class="p3-quote-bar"></span>
      <div class="p3-quote-text">Ich bin die Subline.<br>Xim que quuntis quam fugit<br>et, tem aliqui cum enditia<br>volo qui recto quas et</div>
    </div>
    <div class="member" style="left:36px">
      <div class="avatar" role="img" aria-label="Porträtfoto"></div>
      <div class="member-name">NAME <span>POSITION</span></div>
      <p>Est quate dolorro ommoluptate voloreptate doles esequas quis sincit ulpario. Neque erate re, sam, siti volorer cimodis desto magnis.</p>
    </div>
    <div class="member" style="left:116px;top:200px">
      <div class="avatar" role="img" aria-label="Porträtfoto"></div>
      <div class="member-name">NAME <span>POSITION</span></div>
      <p>Est quate dolorro ommoluptate voloreptate doles esequas quis sincit ulpario. Neque erate re, sam, siti volorer cimodis desto magnis.</p>
    </div>
    <div class="brand"><span class="brand-dot"></span>GZR <span class="brand-small-sub">Gründerzentrum<br>Rheinau</span></div>
  </div>
</section>

</body>
</html>
```